Business Card Design for Occupational Medicine Start Up Company

We need to design a professional business card. We are a healthcare company providing occupational medicine services to blue collar industries. We are professional, efficient and high quality service providers.

Target Market(s)

Blue Collar Industry: Shipbuilding, Ports, Trucking Companies; The Executives and Safety Officers for these companies

Industry/Entity Type

Healthcare

Contact Information for Business Card

Logo, Name, Title, Email, Phone

Other font styles liked:
• Please match our Brand Guide

Requirements
Must have
• Our Company Colors and Logo

```html
<!DOCTYPE html>
<html lang="en">
<head>
<meta charset="UTF-8">
<title>Harborline Clinics – Business Card</title>
<link href="https://fonts.googleapis.com/css2?family=Montserrat:wght@400;500;700&display=swap" rel="stylesheet">
<style>
  :root {
    --navy: #2b3183;
    --navy-deep: #222873;
    --sky: #27a8e0;
    --amber: #f6ae3f;
    --white: #ffffff;
    --backdrop: #e9eaee;
  }
  html, body {
    margin: 0;
    padding: 0;
    width: 1200px;
    height: 874px;
    overflow: hidden;
    background: var(--backdrop);
    font-family: "Montserrat", sans-serif;
  }
  .canvas {
    position: relative;
    width: 1200px;
    height: 874px;
  }
  .card {
    position: absolute;
    left: 250px;
    width: 700px;
    height: 400px;
    border-radius: 22px;
    overflow: hidden;
    box-shadow: 0 8px 24px rgba(20, 24, 60, 0.18);
  }
  .card-back { top: 24px; background: var(--navy); }
  .card-front { top: 450px; background: var(--white); }

  .back-field {
    position: absolute;
    inset: 0;
    background: linear-gradient(135deg, var(--navy-deep) 0%, var(--navy) 45%, #3a44a3 100%);
  }
  .back-name {
    position: absolute;
    right: 40px;
    bottom: 36px;
    display: flex;
    align-items: center;
    gap: 8px;
    font-weight: 700;
    font-size: 15px;
    letter-spacing: 1px;
    color: var(--white);
  }
  .back-name .dot,
  .brand .dot {
    display: inline-block;
    border-radius: 50%;
    background: var(--amber);
  }
  .back-name .dot { width: 14px; height: 14px; }

  .front-shape { position: absolute; inset: 0; }

  .brand {
    position: absolute;
    top: 78px;
    left: 0;
    right: 0;
    display: flex;
    justify-content: center;
    align-items: center;
    gap: 16px;
    font-weight: 700;
    font-size: 40px;
    letter-spacing: 1px;
    color: var(--navy);
  }
  .brand .dot { width: 44px; height: 44px; }

  .holder {
    position: absolute;
    left: 48px;
    top: 282px;
    width: 250px;
    text-align: right;
  }
  .holder-name {
    font-weight: 700;
    font-size: 26px;
    color: var(--amber);
    letter-spacing: 0.5px;
  }
  .holder-title {
    margin-top: 4px;
    font-size: 17px;
    color: var(--white);
  }
  .divider {
    position: absolute;
    left: 318px;
    top: 280px;
    width: 2px;
    height: 80px;
    background: var(--amber);
  }
  .contacts {
    position: absolute;
    left: 340px;
    top: 276px;
    margin: 0;
    padding: 0;
    list-style: none;
    color: var(--white);
    font-size: 16px;
  }
  .contacts li {
    display: flex;
    align-items: center;
    gap: 9px;
    height: 29px;
  }
  .contacts svg { width: 14px; height: 14px; fill: var(--amber); flex: none; }
</style>
</head>
<body>
<main class="canvas">

  <section class="card card-back" aria-label="Card back">
    <div class="back-field" role="img" aria-label="Tonal repeating brand pattern on navy"></div>
    <div class="back-name"><span class="dot"></span>HARBORLINE</div>
  </section>

  <section class="card card-front" aria-label="Card front">
    <svg class="front-shape" viewBox="0 0 700 400" preserveAspectRatio="none" aria-hidden="true">
      <path d="M0,196 Q330,166 700,330 L700,400 L0,400 Z" fill="var(--sky)"/>
      <path d="M0,206 Q330,178 700,344 L700,400 L0,400 Z" fill="var(--white)"/>
      <path d="M0,212 Q330,186 700,352 L700,400 L0,400 Z" fill="var(--amber)"/>
      <path d="M0,222 Q330,198 700,366 L700,400 L0,400 Z" fill="var(--navy)"/>
    </svg>

    <div class="brand"><span class="dot"></span>HARBORLINE CLINICS</div>

    <div class="holder">
      <div class="holder-name">MARK DELANEY</div>
      <div class="holder-title">President</div>
    </div>
    <div class="divider"></div>

    <ul class="contacts">
      <li>
        <svg viewBox="0 0 24 24"><path d="M6.6 10.8a15.1 15.1 0 0 0 6.6 6.6l2.2-2.2a1 1 0 0 1 1-.25 11.4 11.4 0 0 0 3.6.57 1 1 0 0 1 1 1V20a1 1 0 0 1-1 1A17 17 0 0 1 3 4a1 1 0 0 1 1-1h3.5a1 1 0 0 1 1 1c0 1.25.2 2.45.57 3.57a1 1 0 0 1-.25 1z"/></svg>
        555-014-2870
      </li>
      <li>
        <svg viewBox="0 0 24 24"><path d="M2 5h20v14H2z M2 5l10 8 10-8" /></svg>
        mark@harborlineclinics.com
      </li>
      <li>
        <svg viewBox="0 0 24 24"><circle cx="12" cy="12" r="10"/></svg>
        www.harborlineclinics.com
      </li>
    </ul>
  </section>

</main>
</body>
</html>
```